Need Help having my business card stand out

I am the owner of Birchway Canine Training and would like for my business cards to stand out. I have been trying to keep designing them myself but I can't get what I have in my head on the card. I will try my best to post templates that I like for inspirations. I want something unique but elegant. I don't want in to look cartoony or cheesy. It needs to pop in a pet shop but also in a coffee shop or gym.

Target Market(s)

Dog owners, Married ,No young kids Jr High school kids and up (maybe kids on the way) Executives, Stay at home moms/wives, Small business owners

Industry/Entity Type

Dog Training

Contact Information for Business Card

Lowell Spratt, 281-904-3376, info@birchwaycanine.example, www.birchwaycanine.example

Colors

Designer to choose colors to be used in the design.

Requirements
Must have
• my logo
Should not have
• Cursive lettering

```html
<!DOCTYPE html>
<html lang="en">
<head>
<meta charset="utf-8">
<title>Birchway Canine Training – Business Card</title>
<link href="https://fonts.googleapis.com/css2?family=Open+Sans:wght@300;400;600;700&display=swap" rel="stylesheet">
<style>
  :root {
    --page: #e4e4e4;
    --rose-light: #c17b79;
    --rose: #a95f5e;
    --rose-deep: #8f4a4a;
    --maroon: #5a0f13;
    --maroon-dark: #420a0d;
    --band-text: #b87674;
    --ink-light: #ffffff;
    --line-soft: #d9a5a3;
  }
  * { box-sizing: border-box; margin: 0; padding: 0; }
  html, body {
    width: 1200px; height: 800px; overflow: hidden;
    background: var(--page);
    font-family: "Open Sans", Arial, sans-serif;
  }
  .sheet {
    width: 1200px; height: 800px;
    display: flex; flex-direction: column; align-items: center; justify-content: center;
    gap: 30px;
  }
  .card {
    position: relative;
    width: 630px; height: 360px;
    overflow: hidden;
    background: linear-gradient(120deg, var(--rose-light) 0%, var(--rose) 45%, var(--rose-deep) 100%);
    box-shadow: 0 6px 18px rgba(0,0,0,0.18);
  }
  .card__texture { position: absolute; inset: 0; }
  .band {
    position: absolute; left: 0; right: 0;
    background: linear-gradient(90deg, var(--maroon-dark), var(--maroon) 40%, var(--maroon-dark));
  }

  /* contact side */
  .card--contact .band { top: 64px; height: 42px; }
  .band__tagline {
    position: absolute; right: 28px; top: 50%; transform: translateY(-50%);
    color: var(--band-text); font-weight: 600; font-size: 14px; letter-spacing: 2.5px;
    text-transform: uppercase; white-space: nowrap;
  }
  .contact-rail {
    position: absolute; left: 338px; top: 106px; width: 24px; height: 150px;
    background: linear-gradient(180deg, var(--maroon-dark), var(--maroon));
  }
  .contact-rail svg { position: absolute; left: 0; top: 0; }
  .contact-list {
    position: absolute; left: 374px; top: 116px;
    list-style: none; color: var(--ink-light);
    font-size: 11px; line-height: 21px; font-weight: 400;
    white-space: nowrap;
  }
  .person { position: absolute; left: 70px; top: 240px; color: var(--ink-light); }
  .person__name { font-size: 26px; line-height: 30px; }
  .person__first { font-weight: 700; }
  .person__last { font-weight: 300; }
  .person__role { font-size: 18px; font-weight: 300; line-height: 22px; }

  /* brand side */
  .card--brand .band { top: 178px; height: 48px; }
  .brand {
    position: absolute; right: 36px; top: 118px;
    display: flex; align-items: center; gap: 12px;
  }
  .brand__mark { width: 34px; height: 34px; border-radius: 50%; background: var(--maroon); }
  .brand__name { color: var(--maroon); font-weight: 700; font-size: 24px; letter-spacing: 0.3px; white-space: nowrap; }
  .tagline {
    position: absolute; right: 36px; top: 250px;
    display: flex; align-items: center; gap: 16px;
    color: var(--ink-light); font-weight: 600; font-size: 15px; letter-spacing: 2.5px;
    text-transform: uppercase; white-space: nowrap;
  }
  .tagline::before { content: ""; width: 50px; height: 2px; background: var(--line-soft); }
  .accent-line { position: absolute; height: 2px; background: var(--line-soft); opacity: 0.8; }
  .accent-line--right { right: 36px; top: 201px; width: 60px; }
  .accent-line--left { left: 60px; top: 201px; width: 80px; }
</style>
</head>
<body>
<main class="sheet">

  <section class="card card--contact" aria-label="Business card, contact side">
    <div class="card__texture" role="img" aria-label="Fine diagonal rose pinstripe texture"></div>
    <div class="band"><span class="band__tagline">Your dog trainer for life</span></div>

    <div class="contact-rail">
      <svg width="24" height="150" viewBox="0 0 24 150" aria-hidden="true">
        <g fill="#ffffff">
          <path d="M12 12c-2.6 0-4.5 2-4.5 4.4 0 3.3 4.5 7.6 4.5 7.6s4.5-4.3 4.5-7.6C16.5 14 14.6 12 12 12zm0 6a1.6 1.6 0 1 1 0-3.2 1.6 1.6 0 0 1 0 3.2z"/>
          <path d="M7 43c0-1 .8-1.8 1.8-1.8h6.4c1 0 1.8.8 1.8 1.8v1.2h-3v-1h-4v1H7z"/>
          <rect x="7.5" y="45.5" width="9" height="5.5" rx="1"/>
          <rect x="6.5" y="69" width="11" height="8" rx="1"/>
        </g>
        <path d="M6.8 69.5 12 74l5.2-4.5" fill="none" stroke="#5a0f13" stroke-width="1.2"/>
        <g fill="none" stroke="#ffffff" stroke-width="1.2">
          <circle cx="12" cy="100" r="5.5"/>
          <ellipse cx="12" cy="100" rx="2.4" ry="5.5"/>
          <line x1="6.5" y1="100" x2="17.5" y2="100"/>
        </g>
      </svg>
    </div>

    <ul class="contact-list">
      <li>000 Alder Row, Suite 300, Harlow, US 0000</li>
      <li>281-904-3376</li>
      <li>info@birchwaycanine.example</li>
      <li>www.birchwaycanine.example</li>
    </ul>

    <div class="person">
      <p class="person__name"><span class="person__first">Lowell</span> <span class="person__last">Spratt</span></p>
      <p class="person__role">Founder</p>
    </div>
  </section>

  <section class="card card--brand" aria-label="Business card, brand side">
    <div class="card__texture" role="img" aria-label="Fine diagonal rose pinstripe texture"></div>
    <div class="band"></div>
    <span class="accent-line accent-line--left"></span>
    <span class="accent-line accent-line--right"></span>

    <div class="brand">
      <span class="brand__mark"></span>
      <span class="brand__name">Birchway Canine Training</span>
    </div>

    <p class="tagline">Your dog trainer for life</p>
  </section>

</main>
</body>
</html>
```